Website design for Puddle Jump Kidscare

I need a website designed for my daycare business, Puddle Jump Kidscare, now that I have a new logo. My former website was ok but simple and I did not have a logo yet. It also was created by me using a template and was entirely pink. I loved the bright, happy feel of it but worried it might not appeal as much to potential clients who have sons. Therefore, I need a site which will appeal to both genders while still keeping the cheerful color scheme of my new logo, which has pinks, blue, green and cream.
Updates

Reason: Hello! I am still trying to download my new logo and am sorry it is taking me so long. Hopefully I will it posted by the end of today (US Eastern Standard Time). Thank you all very much for your patience!

Hello! I have finally managed to upload my new logo for you to use in designing my website. I'm sorry it took so long and greatly appreciate your time and creative efforts! I look forward to seeing what is submitted based on my logo design and its style/colors.

Many thanks!

Reason: As I've been traveling and posted my logo file late, I am extending my deadline. I am now back and can focus on providing more and better feedback. I appreciate your patience and submissions very much!

Reason: I need more time to provide feedback and make decisions.

Industry/Entity Type

Daycare

Colors
0192cd
33a6d7
86cae7
cadf82
fbf289
add136
e34197

```html
<!DOCTYPE html>
<html lang="en">
<head>
<meta charset="utf-8">
<title>Puddle Jump Kidscare</title>
<link rel="stylesheet" href="https://fonts.googleapis.com/css2?family=Open+Sans:ital,wght@0,400;0,600;0,700;1,400;1,600&display=swap">
<style>
  :root {
    --pink: #b02a5e;
    --pink-dark: #9c1f50;
    --magenta: #a81d55;
    --green: #8fb22a;
    --brown: #5b3d1e;
    --blue-link: #1a9ad6;
    --badge: #9ccfdc;
    --badge-foot: #5e5e5e;
    --text: #3b3b3b;
    --muted: #555;
    --rule: #dcdcdc;
    --footer: #ececec;
    --cream: #f3efe8;
  }
  * { box-sizing: border-box; margin: 0; padding: 0; }
  html, body { width: 943px; height: 1200px; overflow: hidden; }
  body {
    position: relative;
    font-family: "Open Sans", Arial, sans-serif;
    color: var(--text);
    background: linear-gradient(180deg, #f6eef1 0%, #f7f3f4 200px, #fafafa 420px, #ffffff 700px);
  }
  .abs { position: absolute; }

  /* Brand */
  .brand {
    left: 0; width: 943px; top: 60px; text-align: center;
    font-size: 34px; font-weight: 700; color: var(--pink); letter-spacing: -0.5px;
    display: flex; justify-content: center; align-items: center; gap: 10px;
  }
  .brand-dot { width: 18px; height: 18px; border-radius: 50%; background: var(--green); }

  /* Navigation */
  .main-nav {
    left: 134px; top: 173px; width: 674px; height: 42px;
    background: linear-gradient(180deg, #bb3268, var(--pink-dark));
    border-radius: 3px 3px 0 0;
    display: flex; align-items: center;
  }
  .main-nav a {
    color: #fff; text-decoration: none; font-size: 9.6px; font-weight: 600;
    height: 42px; line-height: 42px; padding: 0 16px;
    border-right: 1px solid rgba(255,255,255,0.12);
  }
  .main-nav a:first-child { padding-left: 28px; }
  .main-nav a:last-child { border-right: 0; }

  /* Slider */
  .hero {
    left: 134px; top: 215px; width: 674px; height: 324px;
    background: radial-gradient(ellipse at 50% 45%, #eeeceb 0%, #dcd9d7 70%, #cfcbc8 100%);
  }
  .slide-arrow {
    top: 147px; width: 39px; height: 39px; background: rgba(255,255,255,0.85);
    display: flex; align-items: center; justify-content: center;
  }
  .slide-arrow.prev { left: 0; }
  .slide-arrow.next { right: 0; }

  /* Feature boxes */
  .feature { top: 562px; width: 216px; height: 244px; color: #fff; text-align: center; }
  .feature svg.shape { position: absolute; left: 0; top: 0; }
  .feature .icon {
    position: absolute; left: 60px; top: 32px; width: 96px; height: 96px; border-radius: 50%;
    background: radial-gradient(circle at 45% 40%, #ffffff, var(--cream));
    box-shadow: 0 0 0 4px rgba(255,255,255,0.25);
  }
  .feature h3 {
    position: absolute; left: 0; right: 0; top: 142px;
    font-size: 12px; font-weight: 400; font-style: italic; letter-spacing: 0.4px;
  }
  .feature p {
    position: absolute; left: 18px; right: 18px; top: 172px;
    font-size: 7.8px; font-style: italic; font-weight: 600; line-height: 14.8px; opacity: 0.92;
  }
  .f-learning { left: 134px; }
  .f-creativity { left: 364px; }
  .f-sharing { left: 593px; }

  /* Lower columns */
  .col-title { font-size: 12.4px; font-weight: 400; color: #222; }
  .col-title em { color: var(--magenta); font-weight: 700; }
  .welcome { left: 134px; top: 834px; width: 208px; }
  .welcome-photo {
    margin-top: 13px; width: 208px; height: 118px; border: 1px solid #ddd;
    background: linear-gradient(135deg, #f2eeee, #d9d3d6 55%, #c9c6cc);
  }
  .welcome p { margin-top: 19px; font-size: 8.2px; line-height: 15px; color: var(--muted); }
  .read-more { display: flex; align-items: center; gap: 5px; margin-top: 19px; font-size: 8.2px; color: #333; }
  .read-more span { width: 5px; height: 5px; border-radius: 50%; background: #f39a1e; }

  .services { left: 372px; top: 836px; width: 207px; }
  .services p { margin-top: 23px; font-size: 8.2px; line-height: 15px; color: #333; text-align: justify; }
  .service-list { list-style: none; margin-top: 26px; }
  .service-list li {
    font-size: 8.2px; color: var(--blue-link); height: 34px; line-height: 14px;
    border-bottom: 1px solid var(--rule); padding: 8px 0 0 14px; position: relative;
  }
  .service-list li:first-child { padding-top: 0; height: 26px; }
  .service-list li::before { content: "›"; position: absolute; left: 0; color: #666; }

  .news { left: 612px; top: 833px; width: 198px; }
  .news .col-title { padding-bottom: 12px; border-bottom: 1px solid var(--rule); }
  .event { display: flex; gap: 18px; margin-top: 12px; height: 71px; }
  .event + .event { margin-top: 12px; }
  .date { width: 37px; flex: none; position: relative; }
  .date .day {
    height: 50px; background: var(--badge); color: #fff; text-align: center;
    font-size: 13px; line-height: 14px; padding-top: 8px;
  }
  .date .day small { display: block; font-size: 8px; margin-top: 10px; }
  .date .day::after {
    content: ""; position: absolute; right: -6px; top: 10px;
    border-left: 6px solid var(--badge); border-top: 6px solid transparent; border-bottom: 6px solid transparent;
  }
  .date .talk { height: 21px; background: var(--badge-foot); display: flex; align-items: center; justify-content: center; }
  .event h4 { font-size: 11.6px; font-weight: 400; color: #222; margin-top: -2px; }
  .event p { margin-top: 9px; font-size: 7.8px; line-height: 14.8px; color: var(--muted); text-align: justify; }

  /* Footer */
  .site-footer {
    left: 0; top: 1150px; width: 943px; height: 50px; background: var(--footer);
    border-top: 1px solid #e0e0e0;
  }
  .foot-nav { left: 134px; top: 19px; font-size: 8.4px; color: #333; word-spacing: 1px; }
  .social { left: 455px; top: 12px; display: flex; gap: 4px; }
  .social span { width: 20px; height: 20px; border-radius: 50%; background: #4b4b4b; border: 2px solid #d7b04b; }
  .copyright { left: 566px; top: 19px; font-size: 8.2px; color: #444; }
</style>
</head>
<body>

<header>
  <div class="abs brand"><span class="brand-dot"></span>Puddle Jump Kidscare</div>
  <nav class="abs main-nav">
    <a href="#">HOME</a><a href="#">ABOUT</a><a href="#">SERVICES</a><a href="#">HOURS AND FEES</a>
    <a href="#">POLICIES</a><a href="#">PHOTOS</a><a href="#">TESTIMONIALS</a><a href="#">CONTACT US</a>
  </nav>
</header>

<section class="abs hero" role="img" aria-label="Photo of two toddlers playing with a ring stacking toy">
  <div class="abs slide-arrow prev">
    <svg width="12" height="16" viewBox="0 0 12 16"><path d="M9 2 L3 8 L9 14" fill="none" stroke="#333" stroke-width="2.6"/></svg>
  </div>
  <div class="abs slide-arrow next">
    <svg width="12" height="16" viewBox="0 0 12 16"><path d="M3 2 L9 8 L3 14" fill="none" stroke="#333" stroke-width="2.6"/></svg>
  </div>
</section>

<section class="abs feature f-learning">
  <svg class="shape" width="216" height="244" viewBox="0 0 216 244"><path d="M0 22 Q20 0 60 2 Q90 4 110 12 Q140 -2 175 6 Q195 12 216 18 L216 244 L0 244 Z" fill="var(--green)"/></svg>
  <div class="icon" role="img" aria-label="Illustration of a stack of books with an apple"></div>
  <h3>LEARNING</h3>
  <p>We develop age-appropriate activities that intro- duce and strengthen academic and social skills.We develop age-appropriate activities that introduce and strengthen</p>
</section>

<section class="abs feature f-creativity">
  <svg class="shape" width="216" height="244" viewBox="0 0 216 244"><path d="M0 22 Q30 -2 70 4 Q100 10 130 6 Q170 0 200 12 Q210 16 216 20 L216 244 L0 244 Z" fill="var(--magenta)"/></svg>
  <div class="icon" role="img" aria-label="Illustration of a paint palette and brush"></div>
  <h3>CREATIVITY</h3>
  <p>We offer children a wide range of creative oppor- tunities including art projects, toddler yoga lessons, afternoon tea parties, dress up play, and a large selection of books and games.</p>
</section>

<section class="abs feature f-sharing">
  <svg class="shape" width="216" height="244" viewBox="0 0 216 244"><path d="M0 22 Q25 6 60 6 Q95 2 120 8 Q160 -2 195 8 Q208 14 216 22 L216 244 L0 244 Z" fill="var(--brown)"/></svg>
  <div class="icon" role="img" aria-label="Illustration of coloured pencils arranged in a circle"></div>
  <h3>SHARING</h3>
  <p>We develop age-appropriate activities that intro- duce and strengthen academic and social skills.We develop age-appropriate activities that introduce and strengthen</p>
</section>

<section class="abs welcome">
  <h2 class="col-title">Welcome to <em>Puddle Jump Kidscare</em></h2>
  <div class="welcome-photo" role="img" aria-label="Photo of two toddlers building with coloured blocks"></div>
  <p>Welcome to Puddle Jump Kidscare, a licensed Group Family Day Care, located in Maple Harbor's beautiful Northside. We are located on a pretty, tree-lined block on Willow Lane, between Oak and Birch Avenues. We are a few blocks from the Green line tram and the Elm Road bus route, and we offer flexible</p>
  <div class="read-more">Read more <span></span></div>
</section>

<section class="abs services">
  <h2 class="col-title">Services We Provide</h2>
  <p>Lorem ipsum dolor sit amet, consectetuer adipiscing elit, sed diam nonummy nibh euismod tincidunt ut laoreet dolore magna aliquam erat volutpat. Ut wisi enim ad minim veniam.</p>
  <ul class="service-list">
    <li>Flexible hourly full and part-time childcare</li>
    <li>Discount for siblings</li>
    <li>Small adult: child ratio</li>
    <li>Daily schedules that vary per the age of children</li>
    <li>Large selection of books</li>
  </ul>
</section>

<section class="abs news">
  <h2 class="col-title">News &amp; Events</h2>
  <article class="event">
    <div class="date"><div class="day">15<small>OCT</small></div><div class="talk"><svg width="11" height="9" viewBox="0 0 11 9"><ellipse cx="5.5" cy="4" rx="5" ry="3.6" fill="#fff"/><path d="M2 6 L1 9 L5 7 Z" fill="#fff"/></svg></div></div>
    <div><h4>Morbi tempor quam</h4><p>Morbi tempor quam vel massa adi piscing ute cursus mi congue pelle ntesque niselit er comte</p></div>
  </article>
  <article class="event">
    <div class="date"><div class="day">15<small>OCT</small></div><div class="talk"><svg width="11" height="9" viewBox="0 0 11 9"><ellipse cx="5.5" cy="4" rx="5" ry="3.6" fill="#fff"/><path d="M2 6 L1 9 L5 7 Z" fill="#fff"/></svg></div></div>
    <div><h4>Set ipsum dolor sit amet</h4><p>Morbi tempor quam vel massa adi piscing ute cursus mi congue pelle ntesque niselit er comte</p></div>
  </article>
  <article class="event">
    <div class="date"><div class="day">15<small>OCT</small></div><div class="talk"><svg width="11" height="9" viewBox="0 0 11 9"><ellipse cx="5.5" cy="4" rx="5" ry="3.6" fill="#fff"/><path d="M2 6 L1 9 L5 7 Z" fill="#fff"/></svg></div></div>
    <div><h4>Magna dolor sit amet</h4><p>Morbi tempor quam vel massa adi piscing ute cursus mi congue pelle ntesque niselit er comte</p></div>
  </article>
</section>

<footer class="abs site-footer">
  <div class="abs foot-nav">HOME &nbsp;&nbsp;| &nbsp;&nbsp;ABOUT US &nbsp;&nbsp;| &nbsp;&nbsp;SERVICES | &nbsp;HOURS AND FEES &nbsp;| &nbsp;CONTACT US</div>
  <div class="abs social"><span></span><span></span><span></span><span></span></div>
  <div class="abs copyright">©2014 2014 &nbsp;PUDDLE JUMP KIDSCARE, ALL RIGHTS RESERVED.</div>
</footer>

</body>
</html>
```